Business Card Design using new attached logo

We are a family run Plumbing and Heating firm looking to improve our company image with an improved business card and new logo.We are looking to keep the company colour (Blue) involved in our design

Reason: New logo added which needs to be incorporated on designs

Industry/Entity Type

Business

Contact Information for Business Card

See attachment of all info required.

Requirements
Must have
• We have just picked a new company logo which is attached.
• Could you please provide your business card designs using this logo.
• We are looking for the logo on the back as well as the front with all the info required

```html
<!DOCTYPE html>
<html lang="en">
<head>
<meta charset="utf-8">
<title>Kestrel Heating Ltd – Business Card</title>
<link rel="stylesheet" href="https://fonts.googleapis.com/css2?family=Roboto:wght@400;700&display=swap">
<style>
  :root {
    --page: #e9ebee;
    --card-blue: #0a78bc;
    --deep-blue: #0b4f86;
    --sky-blue: #1ba6de;
    --navy: #1d3a8a;
    --white: #ffffff;
    --ink: #151515;
    --shadow: rgba(0, 0, 0, 0.18);
  }
  * { margin: 0; padding: 0; box-sizing: border-box; }
  html, body {
    width: 1200px;
    height: 900px;
    overflow: hidden;
    background: var(--page);
    font-family: "Roboto", Arial, sans-serif;
  }
  .canvas {
    width: 1200px;
    height: 900px;
    display: flex;
    flex-direction: column;
    align-items: center;
    justify-content: center;
    gap: 36px;
  }
  .card {
    display: block;
    width: 700px;
    height: 400px;
    box-shadow: 0 8px 22px var(--shadow);
  }
  text { font-family: "Roboto", Arial, sans-serif; }
  .card-bg { fill: var(--card-blue); }
  .deco-frame { fill: none; stroke: var(--deep-blue); stroke-width: 14; }
  .logo-shadow { fill: var(--ink); }
  .logo-border { fill: var(--sky-blue); }
  .logo-panel { fill: var(--white); }
  .logo-name { fill: var(--navy); font-weight: 700; }
  .front-name { fill: var(--white); font-weight: 700; font-size: 13px; letter-spacing: 0.3px; }
  .front-role { fill: var(--white); font-weight: 400; font-size: 10px; }
  .name-panel { fill: var(--white); }
  .panel-edge { fill: var(--ink); }
  .contact-frame { fill: none; stroke: var(--white); stroke-width: 16; }
  .contact-frame-inner { fill: none; stroke: var(--ink); stroke-width: 3; }
  .back-name { fill: var(--ink); font-weight: 700; font-size: 16px; letter-spacing: 0.3px; }
  .back-role { fill: var(--ink); font-weight: 400; font-size: 13px; }
  .contact-line { fill: var(--white); font-weight: 400; font-size: 15.5px; }
</style>
</head>
<body>
<main class="canvas">

  <svg class="card card-front" viewBox="0 0 700 400" width="700" height="400" aria-label="Business card front">
    <defs>
      <clipPath id="front-clip"><rect width="700" height="400"/></clipPath>
    </defs>
    <g clip-path="url(#front-clip)">
      <rect class="card-bg" width="700" height="400"/>
      <g class="side-decoration">
        <polygon class="deco-frame" points="-60,120 90,40 170,160 20,240"/>
        <polygon class="deco-frame" points="-40,250 100,185 175,300 35,370"/>
      </g>
      <g class="logo-block" transform="rotate(12 339 198)">
        <rect class="logo-shadow" x="248" y="62" width="212" height="302"/>
        <rect class="logo-border" x="232" y="46" width="214" height="304"/>
        <rect class="logo-panel" x="248" y="62" width="182" height="272"/>
        <text class="logo-name" x="339" y="188" font-size="34" text-anchor="middle">Kestrel</text>
        <text class="logo-name" x="339" y="226" font-size="22" text-anchor="middle">Heating Ltd</text>
      </g>
      <text class="front-name" x="676" y="30" text-anchor="end">DANIEL HARTLEY</text>
      <text class="front-role" x="676" y="44" text-anchor="end">Director</text>
    </g>
  </svg>

  <svg class="card card-back" viewBox="0 0 700 400" width="700" height="400" aria-label="Business card back">
    <defs>
      <clipPath id="back-clip"><rect width="700" height="400"/></clipPath>
    </defs>
    <g clip-path="url(#back-clip)">
      <rect class="card-bg" width="700" height="400"/>
      <polygon class="panel-edge" points="250,0 274,0 374,110 54,400 30,400 350,110"/>
      <polygon class="name-panel" points="0,0 250,0 350,110 30,400 0,400"/>
      <g class="contact-frame-group">
        <polygon class="contact-frame" points="215,250 700,-10 960,475 475,735"/>
        <polygon class="contact-frame-inner" points="232,255 695,7 943,470 480,718"/>
        <polygon class="contact-frame" points="640,410 720,366 760,440"/>
      </g>
      <text class="back-name" x="150" y="150" text-anchor="middle">DANIEL HARTLEY</text>
      <text class="back-role" x="150" y="168" text-anchor="middle">Director</text>
      <g class="contact-details">
        <text class="contact-line" x="330" y="240">14 Mill Lane, Ashby Road,</text>
        <text class="contact-line" x="330" y="260">Thornbury, Kent TN9 2QA</text>
        <text class="contact-line" x="330" y="280">Tel : 020 7946 0321, Fax.: 020 7946 0388</text>
        <text class="contact-line" x="330" y="300">Mob: 07700 900456</text>
        <text class="contact-line" x="330" y="324">daniel@kestrelheating.co.uk</text>
      </g>
    </g>
  </svg>

</main>
</body>
</html>
```